Senior Benefits checkup postcard

develop oversize postcard for direct mail campaign for senior market insurance agency. Targeting seniors ages 50-80. offering a no cost or free benefits checkup for Life, Health and wealth protection.. Posing questions to seniors Such as. *With over 280 insurance companies in our state, How do you find the right plan?* Can I save money on my vantora plan? Who covers my illnesses? Is my life insurance policy still good? Who has the best smoker rates? Who covers diabetes or COPD with no waiting period? many questions senior can ask themselves, be open.
Prompt clients to call local phone number to schedule their free benefits check up. A state licensed agent will consult seniors in the privacy of their own home. Welcome their children or caregivers to attend.
Updates

Thank you designers for all your hard work and efforts. You have given us many options to chose form and things to discuss.I appreciate your input and suggestions. Keep up the great work you do.

Target Market(s)

Seniors ages 50-80, Life, Health, Vantora, and wealth protection. This is for consumers not agents.

Industry/Entity Type

Insurance

Font styles to use
Sans Serif

Requirements
Must have
• Phone number to call in. Company logo, area for mailing label.and postage.
Nice to have
• Use both sides to market program, photos of seniors. easy to read for older seniors. List of product offering.using attachments listed as business card back.
Should not have
• Cannot use words such as Best, cheapest, lowest, etc
• due to vantora advertising guidelines.

```html
<!DOCTYPE html>
<html lang="en">
<head>
<meta charset="utf-8">
<title>Golden Harbor Benefits – Free Benefits Checkup Postcard</title>
<link href="https://fonts.googleapis.com/css2?family=Open+Sans:wght@400;600;700&display=swap" rel="stylesheet">
<style>
  :root {
    --navy: #2a4d86;
    --red: #d23a3f;
    --page-bg: #e9e9eb;
    --card-white: #ffffff;
    --panel-grey: rgba(150, 152, 158, 0.55);
    --band-grey: rgba(120, 130, 145, 0.45);
    --rule-grey: #cfd0d4;
    --text-dark: #3b3f47;
    --text-light: #ffffff;
    --sky-top: #b9d3ea;
    --sky-mid: #dde9f3;
    --sky-low: #c7d3de;
  }
  * { box-sizing: border-box; margin: 0; padding: 0; }
  html, body {
    width: 1200px; height: 856px; overflow: hidden;
    background: var(--page-bg);
    font-family: "Open Sans", Arial, sans-serif;
  }
  .canvas {
    position: relative; width: 1200px; height: 856px;
    display: flex; align-items: center; justify-content: center; gap: 40px;
  }
  .postcard {
    position: relative; width: 560px; height: 374px; overflow: hidden;
    background: var(--card-white);
    box-shadow: 0 2px 10px rgba(0,0,0,0.12);
  }
  .brand-mark { width: 14px; height: 14px; background: var(--red); flex: none; }
  .brand-name {
    color: var(--navy); font-weight: 600; text-transform: uppercase; line-height: 1.05;
  }

  /* ---------- Back side ---------- */
  .back-photo {
    position: absolute; left: 170px; top: 40px; width: 240px; height: 230px;
    background: radial-gradient(ellipse at 50% 45%, #ede8e2 0%, #f5f3f0 55%, rgba(255,255,255,0) 75%);
  }
  .back-brand {
    position: absolute; left: 26px; top: 28px; display: flex; align-items: center; gap: 10px;
  }
  .back-brand .brand-name { font-size: 15px; letter-spacing: 0.5px; }
  .back-tagline {
    position: absolute; left: 26px; top: 74px;
    font-size: 8.5px; letter-spacing: 0.8px; text-transform: uppercase; color: var(--navy);
  }
  .checkup-questions {
    position: absolute; left: 318px; top: 26px; width: 216px; color: var(--text-dark);
  }
  .checkup-title {
    font-size: 13px; font-weight: 700; color: var(--navy); line-height: 1.25;
  }
  .question-list { list-style: none; margin-top: 8px; }
  .question-list li {
    font-size: 10px; line-height: 14px; margin-bottom: 5px;
    padding-left: 10px; position: relative;
  }
  .question-list li::before {
    content: "?"; position: absolute; left: 0; top: 0;
    color: var(--red); font-weight: 700;
  }
  .checkup-note { font-size: 9.5px; line-height: 13px; color: var(--navy); margin-top: 4px; }
  .mailing-line {
    position: absolute; left: 330px; right: 30px; top: 205px; height: 1px; background: var(--rule-grey);
  }
  .back-panel {
    position: absolute; left: 0; top: 118px; width: 300px; height: 256px;
    background: var(--panel-grey); padding: 20px 14px 0 20px; color: var(--text-dark);
  }
  .offer-list { list-style: none; }
  .offer-list li {
    display: flex; align-items: center; gap: 8px;
    font-size: 11px; line-height: 22px; white-space: nowrap;
  }
  .offer-list li::before {
    content: ""; width: 7px; height: 7px; background: var(--red); flex: none;
  }
  .back-phone {
    display: flex; align-items: center; gap: 10px; margin-top: 10px;
    color: var(--navy); font-size: 25px; font-weight: 600;
  }
  .back-url { margin-top: 10px; font-size: 11px; color: var(--text-dark); }

  /* ---------- Front side ---------- */
  .front-photo {
    position: absolute; inset: 0;
    background: linear-gradient(180deg, var(--sky-top) 0%, var(--sky-mid) 45%, var(--sky-low) 100%);
  }
  .front-offer {
    position: absolute; left: 28px; top: 28px; width: 300px; color: var(--navy);
  }
  .front-offer-title { font-size: 22px; font-weight: 700; line-height: 1.15; }
  .front-offer-lead { font-size: 12px; line-height: 17px; margin-top: 8px; color: var(--text-dark); }
  .front-brand {
    position: absolute; right: 26px; top: 24px; display: flex; align-items: flex-start; gap: 12px;
  }
  .front-brand .brand-mark { width: 22px; height: 22px; margin-top: 6px; }
  .front-brand .brand-name { font-size: 26px; letter-spacing: 1px; text-align: right; }
  .front-tagline {
    position: absolute; right: 26px; top: 120px;
    font-size: 10.5px; letter-spacing: 1px; text-transform: uppercase; color: var(--navy);
  }
  .front-band {
    position: absolute; left: 0; right: 0; top: 220px; bottom: 0;
    background: var(--band-grey); padding: 18px 28px 0 28px; color: var(--text-light);
  }
  .front-phone {
    display: flex; align-items: center; gap: 14px;
    font-size: 42px; font-weight: 400; line-height: 1;
  }
  .front-details { margin: 14px 0 0 58px; font-size: 10.5px; line-height: 15px; }
</style>
</head>
<body>
<main class="canvas">

  <section class="postcard postcard-back" aria-label="Postcard back">
    <div class="back-photo" role="img" aria-label="Faint photo of a smiling senior woman"></div>
    <div class="back-brand">
      <span class="brand-mark"></span>
      <span class="brand-name">Golden Harbor<br>Benefits</span>
    </div>
    <p class="back-tagline">Life, Health and Wealth Protection</p>
    <div class="checkup-questions">
      <p class="checkup-title">Ask yourself during your free checkup:</p>
      <ul class="question-list">
        <li>With over 280 insurers in our state, how do I find the right plan?</li>
        <li>Can I save money on my Vantora plan?</li>
        <li>Is my life insurance policy still good?</li>
        <li>Who covers diabetes or COPD with no waiting period?</li>
      </ul>
    </div>
    <div class="mailing-line"></div>
    <div class="back-panel">
      <ul class="offer-list">
        <li>Life Insurance / Final Expense coverage.</li>
        <li>Vantora Supplements / Vantora Advantage.</li>
        <li>Health Insurance / Affordable Care Act.</li>
        <li>Wealth protection - IRA/401k rollover.</li>
        <li>Wealth transfer - avoid probate &amp; estate taxes.</li>
        <li>Legacy Start Savings program.</li>
      </ul>
      <p class="back-phone">
        <svg width="24" height="24" viewBox="0 0 24 24" aria-hidden="true">
          <circle cx="12" cy="12" r="11" fill="none" stroke="currentColor" stroke-width="2"/>
          <path d="M8 6.5c-.8.6-1.4 1.6-1 3 .8 3 3.5 6 6.5 7 1.3.4 2.4-.2 3-1l-2-2-1.5 1c-1.6-.7-3-2.2-3.7-3.8l1-1.5z" fill="currentColor"/>
        </svg>
        803-555-0147
      </p>
      <p class="back-url">http://goldenharbor.example/benefits/</p>
    </div>
  </section>

  <section class="postcard postcard-front" aria-label="Postcard front">
    <div class="front-photo" role="img" aria-label="Photo of a happy senior couple embracing under a bright sky"></div>
    <div class="front-offer">
      <p class="front-offer-title">Call for your FREE<br>Benefits Checkup</p>
      <p class="front-offer-lead">A state licensed agent visits you at home.<br>Children and caregivers are welcome.</p>
    </div>
    <div class="front-brand">
      <span class="brand-mark"></span>
      <span class="brand-name">Golden<br>Harbor<br>Benefits</span>
    </div>
    <p class="front-tagline">Life, Health and Wealth Protection</p>
    <div class="front-band">
      <p class="front-phone">
        <svg width="44" height="44" viewBox="0 0 24 24" aria-hidden="true">
          <circle cx="12" cy="12" r="11" fill="none" stroke="currentColor" stroke-width="1.4"/>
          <path d="M8 6.5c-.8.6-1.4 1.6-1 3 .8 3 3.5 6 6.5 7 1.3.4 2.4-.2 3-1l-2-2-1.5 1c-1.6-.7-3-2.2-3.7-3.8l1-1.5z" fill="currentColor"/>
        </svg>
        803-555-0147
      </p>
      <p class="front-details">
        Address: 1450 Birchline Commons Dr, Suite 210,<br>
        Fairview, NC 28730<br>
        http://goldenharbor.example/benefits/
      </p>
    </div>
  </section>

</main>
</body>
</html>
```